Psychotherapy, Life Coaching, Writer, Motivational Speaker

I am a psychotherapist, life coach, writer and speaker on health and wellness issues. I am a humanist - who believes that we are born to self-actualize - but life - changes that course. That we develop armor and coping mechanisms that divert our growth. I help people examine their road blocks to happiness. My business is unique in that I do concierge therapy. I work intensively - with multi-day sessions, I work internationally through tele-therapy - and traditionally - in an office space. My work is tailored to your needs.

Target Market(s)

Broad

Industry/Entity Type

Health

Contact Information for Business Card

Listen And Grow
Sam Perriton
248 East 39th Street
New York, NY 10027
(305) 555-0173

Requirements
Must have
• Clean lines... not too busy...
• FB page listing: Listen And Grow
• my Web page: www.listenandgrow-example.com
Nice to have
• I would love to be able to list the services: Psychotherapist, Life Coach, Motivational Speaker and Writer - but also don't want a crazy crowded card. Feel free to use the back for description.
Should not have
• Stay away from corny imagery - lotus flowers, zen, lily pond, clouds.

```html
<!DOCTYPE html>
<html lang="en">
<head>
<meta charset="utf-8">
<title>Listen And Grow – Business Card</title>
<link href="https://fonts.googleapis.com/css2?family=Lato:wght@400;700;900&display=swap" rel="stylesheet">
<style>
  :root {
    --backdrop: #e9e9e9;
    --card-white: #ffffff;
    --brand-blue: #4a78b5;
    --band-blue-light: #5a87c2;
    --band-blue-dark: #2f5e9f;
    --ink: #111111;
    --panel-black: #050505;
    --light-text: #f2f2f2;
  }
  * { box-sizing: border-box; margin: 0; padding: 0; }
  html, body { width: 1200px; height: 720px; overflow: hidden; }
  body {
    background: var(--backdrop);
    font-family: "Lato", Arial, sans-serif;
    position: relative;
  }
  .card {
    position: absolute;
    top: 241px;
    width: 419px;
    height: 239px;
    background: var(--card-white);
    overflow: hidden;
  }
  .card--front { left: 148px; border-radius: 14px; }
  .card--back { left: 633px; }

  .card__shape { position: absolute; inset: 0; }

  .brand-title {
    position: absolute;
    left: 0; right: 0;
    text-align: center;
    color: var(--brand-blue);
    font-weight: 700;
  }
  .card--front .brand-title { top: 27px; font-size: 23px; }
  .card--back .brand-title { top: 38px; font-size: 20px; }

  .holder {
    position: absolute;
    top: 91px; left: 0; right: 0;
    text-align: center;
  }
  .holder__name { font-size: 15px; font-weight: 900; color: var(--ink); }
  .holder__creds { font-size: 13px; font-weight: 400; color: var(--light-text); }
  .holder__role { font-size: 12.5px; color: var(--light-text); margin-top: 1px; }

  .contact-list {
    position: absolute;
    left: 15px; top: 152px;
    list-style: none;
    color: var(--light-text);
    font-size: 13px;
    line-height: 15.7px;
  }
  .contact-list li { display: flex; align-items: center; gap: 4px; }
  .contact-list svg { width: 11px; height: 11px; flex: none; }

  .address {
    position: absolute;
    right: 11px; top: 173px;
    text-align: right;
    color: var(--light-text);
    font-size: 11.5px;
    line-height: 15px;
    font-style: normal;
  }

  .band {
    position: absolute;
    left: 0; right: 0;
    background: linear-gradient(90deg, var(--band-blue-light), var(--band-blue-dark));
    display: flex; align-items: center; justify-content: center;
  }
  .band--appointment {
    top: 102px; height: 64px;
    font-size: 13.5px; color: var(--ink);
  }
  .band--services {
    top: 206px; height: 33px;
    font-size: 13px; color: var(--light-text);
  }
</style>
</head>
<body>
  <section class="card card--front">
    <svg class="card__shape" viewBox="0 0 419 239" preserveAspectRatio="none" aria-hidden="true">
      <defs>
        <linearGradient id="arcBlue" x1="0" x2="1" y1="0" y2="0">
          <stop offset="0" stop-color="#3563a3"/>
          <stop offset="0.5" stop-color="#4d7cba"/>
          <stop offset="1" stop-color="#5a89c4"/>
        </linearGradient>
      </defs>
      <path d="M0 131 Q209.5 38 419 131 Z" fill="url(#arcBlue)"/>
      <rect x="0" y="131" width="419" height="108" fill="#050505"/>
    </svg>

    <h1 class="brand-title">Listen And Grow</h1>

    <div class="holder">
      <p><span class="holder__name">Sam Perriton,</span> <span class="holder__creds">LMHC, NCC</span></p>
      <p class="holder__role">Psychotherapist.</p>
    </div>

    <ul class="contact-list">
      <li>
        <svg viewBox="0 0 12 12" aria-hidden="true"><path d="M1 3.5C1 2 2.5 1.5 6 1.5S11 2 11 3.5V4.5H8.5V3.5H3.5V4.5H1Z M3 5H9L10.5 10H1.5Z" fill="#4a78b5"/></svg>
        (305) 555-0173
      </li>
      <li>
        <svg viewBox="0 0 12 12" aria-hidden="true"><rect x="1" y="2.5" width="10" height="7" fill="#4a78b5"/><path d="M1.5 3L6 6.5L10.5 3" stroke="#050505" stroke-width="1" fill="none"/></svg>
        sperritonglobal@example.com
      </li>
      <li>
        <svg viewBox="0 0 12 12" aria-hidden="true"><g fill="none" stroke="#4a78b5" stroke-width="1"><circle cx="6" cy="6" r="4.8"/><ellipse cx="6" cy="6" rx="2" ry="4.8"/><path d="M1.2 6H10.8M2 3.5H10M2 8.5H10"/></g></svg>
        www.listenandgrow-example.com
      </li>
      <li>
        <svg viewBox="0 0 12 12" aria-hidden="true"><rect x="1" y="1" width="10" height="10" rx="1.5" fill="#4a78b5"/></svg>
        Listen And Grow
      </li>
    </ul>

    <address class="address">
      248 East 39th Street<br>
      New York, NY 10027
    </address>
  </section>

  <section class="card card--back">
    <h2 class="brand-title">Listen and Grow</h2>
    <div class="band band--appointment">Your Next Appoinment is at...................... at.............. am/pm</div>
    <div class="band band--services">Psychotherapy, Coaching, Wellness Media</div>
  </section>
</body>
</html>
```